Coastline Premier Retreats Business Card Design

Design a business card for Coastline Premier Retreats. Look at the website for colors and reference. Card should have logo, name, title, office number, mobile number, email, URL and a tagline like, "Luxury Hotel & Resort Email Marketing" (This might change).

https://www.coastlinepremierretreats.example

The rest I will leave up to your imagination.

Contact Information for Business Card

Logo, name, title, office number, mobile number, email, URL and a tagline like, "Luxury Hotel & Resort Email Marketing" (This might change).

```html
<!DOCTYPE html>
<html lang="en">
<head>
<meta charset="utf-8">
<title>Coastline Premier Retreats – Business Card</title>
<link href="https://fonts.googleapis.com/css2?family=Montserrat:wght@400;500;700&display=swap" rel="stylesheet">
<style>
  :root {
    --bg: #b9b9b9;
    --card: #1c1c1c;
    --orange: #f07a12;
    --white: #ffffff;
  }
  * { box-sizing: border-box; margin: 0; padding: 0; }
  html, body { width: 1200px; height: 802px; overflow: hidden; }
  body {
    background: linear-gradient(180deg, #d6d6d6 0%, var(--bg) 100%);
    font-family: 'Montserrat', sans-serif;
    position: relative;
  }
  .card {
    position: absolute;
    width: 520px;
    height: 298px;
    background: var(--card);
    border-radius: 22px;
    border-bottom: 5px solid var(--orange);
    box-shadow: 0 18px 30px rgba(0,0,0,0.35);
    overflow: hidden;
  }
  .card--contact { left: 50px; top: 252px; }
  .card--brand { left: 630px; top: 252px; }

  .brand-name {
    display: flex;
    align-items: center;
    gap: 8px;
    color: var(--white);
    font-weight: 700;
    text-transform: uppercase;
    letter-spacing: 0.04em;
    white-space: nowrap;
  }
  .brand-name__square { width: 10px; height: 10px; background: var(--orange); flex: none; }

  .card--contact .brand-name { position: absolute; left: 250px; top: 34px; font-size: 13px; }

  .person { position: absolute; left: 40px; bottom: 50px; }
  .person__name { color: var(--orange); font-weight: 700; font-size: 24px; letter-spacing: 0.03em; text-transform: uppercase; line-height: 1.2; }
  .person__title { color: var(--white); font-size: 13px; margin-top: 2px; }
  .edge-tab { position: absolute; left: 0; bottom: 54px; width: 14px; height: 34px; background: var(--orange); }

  .contact { position: absolute; left: 250px; top: 84px; width: 250px; color: var(--white); font-size: 10.5px; line-height: 1.6; }
  .contact__address { margin-bottom: 10px; }
  .contact__row { display: flex; align-items: center; gap: 7px; white-space: nowrap; }
  .contact__row svg { width: 10px; height: 10px; flex: none; fill: var(--orange); }
  .contact__accent { color: var(--orange); }

  .card--brand .brand-name { position: absolute; left: 0; right: 0; top: 112px; justify-content: center; font-size: 24px; gap: 12px; }
  .card--brand .brand-name__square { width: 16px; height: 16px; }
  .tagline { position: absolute; left: 0; right: 0; top: 210px; text-align: center; color: var(--orange); font-weight: 500; font-size: 15px; letter-spacing: 0.02em; }
</style>
</head>
<body>
  <article class="card card--contact">
    <div class="brand-name"><span class="brand-name__square"></span>Coastline Premier Retreats</div>

    <div class="contact">
      <p class="contact__address">Po Box, 48 Harbor Lane<br>Bayview, CA 90210</p>
      <p class="contact__row">
        <svg viewBox="0 0 10 10"><rect x="2" y="0" width="6" height="10" rx="1"/></svg><span>555.310.4400</span>
      </p>
      <p class="contact__row">
        <svg viewBox="0 0 10 10"><path d="M1 7 Q1 3 5 3 Q9 3 9 7 Z M3 2 h4 v1 h-4z"/></svg><span>+34 600 555 012</span>
      </p>
      <p class="contact__row">
        <svg viewBox="0 0 10 10"><path d="M0 2 h10 v7 h-10z"/></svg><span>info@coastlinepremierretreats.example</span>
      </p>
      <p class="contact__row">
        <svg viewBox="0 0 10 10"><circle cx="5" cy="5" r="5"/></svg><span>www.<span class="contact__accent">coastlinepremierretreats</span>.example</span>
      </p>
    </div>

    <span class="edge-tab"></span>
    <div class="person">
      <h1 class="person__name">Marcus Hale</h1>
      <p class="person__title">CEO/Founder</p>
    </div>
  </article>

  <article class="card card--brand">
    <div class="brand-name"><span class="brand-name__square"></span>Coastline Premier Retreats</div>
    <p class="tagline">Luxury Hotel &amp; Resort Email Marketing</p>
  </article>
</body>
</html>
```